Tobias Ränkel and Co stationary design

Name of business:
Tobias Ränkel and Co

Can be written as:
Tobias Ränkel and Co
Tobias Ränkel & Co
tobias ränkel & co

If broken into letters:
TR&Co
tr&co

We are a Railway Safety Training Company
Our focus is on rail safety, Rail Management, Safety Management, Train Control Training, Accident Investigation.

.

Project Deadline Extended Reason: The original date was set to commence as soon as the logo contest finished. Sketch harbor started the project as soon as it was paid. Added Thursday, May 12, 2016

Target Market(s)

Professionals, CEO's and Managing Directors

Industry/Entity Type

Management Consulting

Font styles to use
Sans Serif

Requirements
Must have
• Professional, Sharp, Creative and modern
• Please note that this is for stationary concept which must include
• - business card
• - letterhead
• - envelope
• - with compliments slip
• - document cover (like book or folder cover)
• - dividers for folders....
• These must all have a common theme or style
Nice to have
• Keep if fresh
Should not have
• Please don't sent just fonts.... Must be creative

```html
<!DOCTYPE html>
<html lang="en">
<head>
<meta charset="utf-8">
<title>Tobias Ränkel &amp; Co — Business Card</title>
<link href="https://fonts.googleapis.com/css2?family=Open+Sans:ital,wght@0,400;0,600;0,700;1,400&display=swap" rel="stylesheet">
<style>
  :root {
    --navy: #1d2d64;
    --red: #c20a26;
    --paper: #f7f7f7;
    --text-grey: #5a5a5a;
    --backdrop: #3d3d3d;
    --white: #ffffff;
  }
  * { box-sizing: border-box; margin: 0; padding: 0; }
  html, body {
    width: 1200px; height: 750px; overflow: hidden;
    background: var(--backdrop);
    font-family: "Open Sans", sans-serif;
  }
  .stage { position: relative; width: 1200px; height: 750px; }
  .card {
    position: absolute; top: 228px;
    width: 461px; height: 262px; overflow: hidden;
  }
  .card--front { left: 124px; background: var(--paper); }
  .card--back { left: 618px; background: var(--red); }

  .brand {
    position: absolute; right: 19px; top: 104px;
    display: flex; align-items: center; gap: 8px;
  }
  .brand__dot { width: 14px; height: 14px; border-radius: 50%; background: var(--red); flex: none; }
  .brand__name { font-size: 17px; font-weight: 700; line-height: 1; color: var(--navy); white-space: nowrap; }

  .person { position: absolute; left: 19px; top: 146px; }
  .person__name { font-size: 16px; font-weight: 600; color: var(--navy); line-height: 21px; }
  .person__role { font-size: 13px; color: var(--red); line-height: 17px; }
  .rule { position: absolute; left: 112px; right: 19px; top: 181px; height: 1px; background: var(--red); }

  .contact { position: absolute; top: 192px; font-size: 12px; color: var(--text-grey); line-height: 17px; }
  .contact--address { left: 19px; }
  .contact--phones { left: 182px; }
  .contact--office { left: 298px; }
  .contact p { white-space: nowrap; }
  .contact__row { display: flex; align-items: center; gap: 6px; }
  .contact__row svg { width: 11px; height: 11px; fill: var(--navy); flex: none; }

  .band-navy { position: absolute; left: 0; bottom: 0; width: 250px; height: 6px; background: var(--navy); }
  .band-red {
    position: absolute; right: 0; bottom: 0; width: 221px; height: 23px;
    background: var(--red); clip-path: polygon(16px 0, 100% 0, 100% 100%, 0 100%);
  }
  .band-red__url {
    position: absolute; right: 24px; top: 3px;
    font-size: 12px; line-height: 17px; font-style: italic; letter-spacing: 0.15em; color: var(--white);
    white-space: nowrap;
  }

  .back-brand {
    position: absolute; left: 0; right: 0; top: 122px;
    display: flex; justify-content: center; align-items: center; gap: 8px;
  }
  .back-brand__dot { width: 14px; height: 14px; border-radius: 50%; background: var(--white); flex: none; }
  .back-brand__name { font-size: 18px; font-weight: 700; line-height: 1; color: var(--white); white-space: nowrap; }
  .back-url {
    position: absolute; left: 0; right: 0; top: 216px; text-align: center;
    font-size: 12px; line-height: 17px; letter-spacing: 0.55em; color: var(--white);
    white-space: nowrap;
  }
</style>
</head>
<body>
<main class="stage">
  <section class="card card--front" aria-label="Business card front">
    <div class="brand">
      <span class="brand__dot"></span>
      <span class="brand__name">Tobias Ränkel &amp; Co</span>
    </div>

    <div class="person">
      <p class="person__name">LENA HARTWIG</p>
      <p class="person__role">CEO/FOUNDER</p>
    </div>
    <div class="rule"></div>

    <div class="contact contact--address">
      <p>4120 Alder Crest Road</p>
      <p>Fairbanks, Alaska 99712</p>
    </div>

    <div class="contact contact--phones">
      <p class="contact__row">
        <svg viewBox="0 0 24 24" aria-hidden="true"><path d="M6.6 10.8a15 15 0 0 0 6.6 6.6l2.2-2.2a1 1 0 0 1 1-.25 11.4 11.4 0 0 0 3.6.57 1 1 0 0 1 1 1V20a1 1 0 0 1-1 1A17 17 0 0 1 3 4a1 1 0 0 1 1-1h3.5a1 1 0 0 1 1 1c0 1.25.2 2.45.57 3.57a1 1 0 0 1-.25 1z"/></svg>
        614 290 5173
      </p>
      <p class="contact__row">
        <svg viewBox="0 0 24 24" aria-hidden="true"><path d="M7 1h10a2 2 0 0 1 2 2v18a2 2 0 0 1-2 2H7a2 2 0 0 1-2-2V3a2 2 0 0 1 2-2zm0 3v14h10V4zm5 15.5a1 1 0 1 0 0 2 1 1 0 0 0 0-2z"/></svg>
        742 518 3069
      </p>
    </div>

    <div class="contact contact--office">
      <p class="contact__row">
        <svg viewBox="0 0 24 24" aria-hidden="true"><path d="M6 2h12v6H6zM3 9h18a2 2 0 0 1 2 2v7h-4v4H5v-4H1v-7a2 2 0 0 1 2-2zm4 8v3h10v-3z"/></svg>
        358 704 2816
      </p>
      <p class="contact__row">
        <svg viewBox="0 0 24 24" aria-hidden="true"><path d="M2 5h20v14H2zm2 2v.5l8 5 8-5V7l-8 5z"/></svg>
        office@trcorail.com
      </p>
    </div>

    <div class="band-navy"></div>
    <div class="band-red"><span class="band-red__url">www.trcorail.com</span></div>
  </section>

  <section class="card card--back" aria-label="Business card back">
    <div class="back-brand">
      <span class="back-brand__dot"></span>
      <span class="back-brand__name">Tobias Ränkel &amp; Co</span>
    </div>
    <p class="back-url">www.trcorail.com</p>
  </section>
</main>
</body>
</html>
```